Professional violinist needs business cards

I am trying to attract the following jobs:
-private violin lessons (primarily classical)
-performance gigs (weddings, birthday parties, funerals, etc.)
-collaborations with other artists (studio recordings, performances)

I want to communicate that I have a very high standard of excellence for my work, but I also love people and celebrations.
Values/style words I like are:
love, joy, peace, fun, beauty, authenticity, excellence, warmth, refined/sleek, free spirited. If that's too confusing, just ignore :)

I will attach my favorite business card template that I could find on Canva. The lines are supposed to be like a music staff, which I think is really cool, but I also don't want it to look too busy. I like the simple black and white--I think it looks sharp--but I also am open to other ideas. I also have seen business cards with pictures included that looked great, so I attached an image that could be used as well.

I am also attaching a file that I made of my initials that could be used as a logo, but I'm not sure if it should be included.

Information on the card:
-My name (18 letters total)
-"violinist"
-phone number, email, website

Thank you!

```html
<!DOCTYPE html>
<html lang="en">
<head>
<meta charset="utf-8">
<title>Danielle Hartwood — Violinist Business Cards</title>
<link rel="stylesheet" href="https://fonts.googleapis.com/css2?family=Dancing+Script:wght@500&family=Cinzel:wght@400&family=Lora:wght@400&display=swap">
<style>
  :root {
    --page: #2a2a2b;
    --card: #202428;
    --card-edge: #1a1d20;
    --ivory: #ecebe6;
    --gold: #cdb998;
    --rule: #b8a688;
    --photo-light: #8a7c62;
    --photo-mid: #5a5142;
    --photo-dark: #2b2723;
  }
  * { margin: 0; padding: 0; box-sizing: border-box; }
  html, body {
    width: 1200px; height: 1138px; overflow: hidden;
    background: var(--page);
  }
  .canvas { position: relative; width: 1200px; height: 1138px; }

  .card {
    position: absolute;
    width: 620px; height: 375px;
    border-radius: 14px;
    background: var(--card);
    overflow: hidden;
    box-shadow: 0 6px 14px rgba(0,0,0,0.45);
  }
  .card--front { left: 274px; top: 186px; }
  .card--back  { left: 276px; top: 608px; }

  .card__photo {
    position: absolute; left: 0; top: 0; bottom: 0;
    width: 240px;
    background:
      linear-gradient(90deg, rgba(32,36,40,0) 70%, var(--card) 100%),
      radial-gradient(ellipse 40% 60% at 45% 60%, var(--photo-dark) 0 60%, transparent 100%),
      linear-gradient(160deg, var(--photo-light), var(--photo-mid) 60%, var(--photo-dark));
  }

  .card__content {
    position: absolute; left: 300px; width: 300px;
    text-align: center;
  }
  .card--front .card__content { top: 120px; }
  .card--back .card__content { top: 74px; }

  .brand {
    display: inline-flex; align-items: center; gap: 7px;
    font-family: "Lora", serif; font-size: 13px;
    color: var(--gold); letter-spacing: 0.5px;
    height: 36px;
  }
  .brand__dot {
    width: 9px; height: 9px; border-radius: 50%;
    background: var(--gold);
  }

  .name {
    font-family: "Dancing Script", cursive; font-weight: 500;
    font-size: 36px; color: var(--ivory);
    margin-top: 20px; line-height: 1;
  }
  .title {
    display: flex; align-items: center; justify-content: center; gap: 14px;
    margin-top: 8px;
    font-family: "Cinzel", serif; font-size: 16px; letter-spacing: 2px;
    color: var(--ivory);
  }
  .title__rule { width: 72px; height: 1px; background: var(--rule); }

  .contact {
    list-style: none; margin-top: 27px;
    font-family: "Lora", serif; font-size: 15px; line-height: 23.5px;
    color: var(--ivory);
  }
  .contact .accent { color: var(--gold); }
</style>
</head>
<body>
<main class="canvas">

  <section class="card card--front">
    <div class="card__photo" role="img" aria-label="Photo of the violinist in a black dress holding her violin and bow beside a stone brick wall"></div>
    <div class="card__content">
      <div class="brand"><span class="brand__dot"></span>Danielle Hartwood</div>
      <h1 class="name">Danielle Hartwood</h1>
      <p class="title"><span class="title__rule"></span>Violinist<span class="title__rule"></span></p>
    </div>
  </section>

  <section class="card card--back">
    <div class="card__photo" role="img" aria-label="Photo of the violinist in a black dress holding her violin and bow beside a stone brick wall"></div>
    <div class="card__content">
      <div class="brand"><span class="brand__dot"></span>Danielle Hartwood</div>
      <h2 class="name">Danielle Hartwood</h2>
      <p class="title"><span class="title__rule"></span>Violinist<span class="title__rule"></span></p>
      <ul class="contact">
        <li>+1 (555) 014-2786</li>
        <li>Danielle@DanielleHartwood.com</li>
        <li>www.<span class="accent">DanielleHartwood</span>.com</li>
        <li>Richmond, VA</li>
      </ul>
    </div>
  </section>

</main>
</body>
</html>
```